Stylish business cards for KV7

To create an appealing and professional business card design for a WOMEN Owned Construction Supply Company.
2 sided card. Incorporate brand elements, curvy, colorful, sleek and bright. No solid white background. attached samples of styles added shapes/ribbons. Want something with that WOW that looks awesome, factor. It is a new logo, so feel free to mess with logo colors in the blue and teal factors that can look good with both dark and light background. If you want to try a watermark with just the KV7, without the "Supply" that might look cool to.

Industry/Entity Type

Women owned construction supply company

Contact Information for Business Card

Name, Title, and phone number and email, web page. maybe spot for qr code.

Font styles to use
Sans Serif

Requirements
Nice to have
• would love to see colors, maybe stylish ribbon dividers or some sort of 2 or 3 tone color card that compliments logo.
Should not have
• Please do not have all white background. Do not include Home/reale state/ or building images.

```html
<!DOCTYPE html>
<html lang="en">
<head>
<meta charset="utf-8">
<title>KV7 Supply – Business Cards</title>
<link rel="stylesheet" href="https://fonts.googleapis.com/css2?family=Figtree:wght@400;700&display=swap">
<style>
  :root {
    --backdrop: #1b1b1c;
    --navy: #1b3a5a;
    --teal: #2194b8;
    --paper: #f4f5f6;
    --white: #ffffff;
    --ghost-light: #dfe3e6;
    --ghost-dark: rgba(255,255,255,0.07);
  }
  * { box-sizing: border-box; margin: 0; padding: 0; }
  html, body {
    width: 1200px; height: 1059px; overflow: hidden;
    background: var(--backdrop);
    font-family: "Figtree", sans-serif;
  }
  .card {
    position: absolute; left: 255px; width: 690px; height: 390px;
    border-radius: 24px; overflow: hidden;
  }
  .card-front { top: 89px; background: var(--paper); }
  .card-back { top: 548px; background: var(--navy); }
  .card-waves { position: absolute; inset: 0; width: 100%; height: 100%; }

  .watermark {
    position: absolute; font-weight: 700; line-height: 1; letter-spacing: -4px;
  }
  .card-front .watermark { left: 18px; top: 18px; font-size: 150px; color: var(--ghost-light); }
  .card-back .watermark { left: 6px; top: 40px; font-size: 300px; color: var(--ghost-dark); }

  .brand-name { position: absolute; font-weight: 700; white-space: nowrap; }
  .card-front .brand-name { left: 380px; top: 78px; font-size: 44px; color: var(--navy); }
  .card-back .brand-name { left: 0; right: 0; top: 160px; text-align: center; font-size: 64px; color: var(--white); }

  .holder { position: absolute; left: 40px; top: 221px; color: var(--white); }
  .holder-name { font-size: 21px; font-weight: 700; color: var(--teal); letter-spacing: 0.5px; }
  .holder-title { font-size: 15px; margin-top: 2px; }

  .contact-list { position: absolute; left: 38px; top: 283px; list-style: none; color: var(--white); font-size: 15.5px; }
  .contact-list li { display: flex; align-items: center; height: 25px; }
  .contact-list svg { width: 13px; height: 13px; margin-right: 7px; fill: none; stroke: var(--teal); stroke-width: 1.6; }
  .contact-list .icon-fill { fill: var(--teal); stroke: none; }

  .address {
    position: absolute; right: 37px; top: 313px; text-align: right;
    color: var(--white); font-size: 15.5px; line-height: 20px; font-style: normal;
  }
</style>
</head>
<body>

<section class="card card-front" aria-label="Front of business card">
  <div class="watermark" aria-hidden="true">KV7</div>
  <svg class="card-waves" viewBox="0 0 690 390" preserveAspectRatio="none" aria-hidden="true">
    <path fill="var(--teal)" d="M0 178 C50 160 120 150 200 160 C320 175 420 222 510 218 C600 214 660 160 690 118 L690 390 L0 390 Z"/>
    <path fill="var(--white)" d="M0 207 C60 189 150 174 230 184 C330 196 420 224 510 220 C600 216 660 199 690 190 L690 390 L0 390 Z"/>
    <path fill="var(--navy)" d="M0 213 C60 195 150 180 230 190 C330 202 420 230 510 226 C600 222 660 205 690 196 L690 390 L0 390 Z"/>
  </svg>
  <div class="brand-name">KV7 Supply</div>

  <div class="holder">
    <p class="holder-name">DANIEL HAYES</p>
    <p class="holder-title">CEO/Founder</p>
  </div>

  <ul class="contact-list">
    <li>
      <svg viewBox="0 0 16 16"><path class="icon-fill" d="M3.5 1.5l2.5 3-1.5 1.8c.9 1.8 2.4 3.3 4.2 4.2L10.5 9l3 2.5-1.6 2.5C6.5 13.6 2.4 9.5 2 4z"/></svg>
      555.310.0482
    </li>
    <li>
      <svg viewBox="0 0 16 16"><rect class="icon-fill" x="1" y="3" width="14" height="10"/><path stroke="var(--navy)" d="M1.5 3.5L8 9l6.5-5.5"/></svg>
      info@kv7supply.com.au
    </li>
    <li>
      <svg viewBox="0 0 16 16"><circle cx="8" cy="8" r="6.5"/><ellipse cx="8" cy="8" rx="2.8" ry="6.5"/><path d="M1.5 8h13M2.5 5h11M2.5 11h11"/></svg>
      www.kv7supply.com.au
    </li>
  </ul>

  <address class="address">
    P.O Box 4127 Harbour Lane<br>
    Westfield QL 40210
  </address>
</section>

<section class="card card-back" aria-label="Back of business card">
  <div class="watermark" aria-hidden="true">KV7</div>
  <div class="brand-name">KV7 Supply</div>
</section>

</body>
</html>
```